Website design for Puddle Jump Kidscare

I need a website designed for my daycare business, Puddle Jump Kidscare, now that I have a new logo. My former website was ok but simple and I did not have a logo yet. It also was created by me using a template and was entirely pink. I loved the bright, happy feel of it but worried it might not appeal as much to potential clients who have sons. Therefore, I need a site which will appeal to both genders while still keeping the cheerful color scheme of my new logo, which has pinks, blue, green and cream.
Updates

Reason: Hello! I am still trying to download my new logo and am sorry it is taking me so long. Hopefully I will it posted by the end of today (US Eastern Standard Time). Thank you all very much for your patience!

Hello! I have finally managed to upload my new logo for you to use in designing my website. I'm sorry it took so long and greatly appreciate your time and creative efforts! I look forward to seeing what is submitted based on my logo design and its style/colors.

Many thanks!

Reason: As I've been traveling and posted my logo file late, I am extending my deadline. I am now back and can focus on providing more and better feedback. I appreciate your patience and submissions very much!

Reason: I need more time to provide feedback and make decisions.

Industry/Entity Type

Daycare

Colors
0192cd
33a6d7
86cae7
cadf82
fbf289
add136
e34197

```html
<!DOCTYPE html>
<html lang="en">
<head>
<meta charset="utf-8">
<title>Puddle Jump Kidscare</title>
<link href="https://fonts.googleapis.com/css2?family=Arimo:ital,wght@0,400;0,700;1,400&display=swap" rel="stylesheet">
<style>
:root{
  --rose:#b24f72;
  --rose-nav:#b5527a;
  --rose-btn:#c9547f;
  --rose-text:#b3476f;
  --blue:#2497cb;
  --ink:#333;
  --ink-soft:#444;
  --band:#e9eaee;
  --footer:#232323;
  --caption:rgba(30,30,30,.88);
}
*{margin:0;padding:0;box-sizing:border-box}
html,body{width:882px;height:1200px;overflow:hidden;background:#fff}
body{position:relative;font-family:"Arimo",Arial,sans-serif;color:var(--ink)}
.abs{position:absolute}

/* header */
.site-header{left:0;top:0;width:882px;height:65px;background:#fff}
.brand{left:126px;top:13px;width:120px;display:flex;align-items:center;gap:6px;color:var(--rose-text);font-size:13px;line-height:15px;font-weight:700}
.brand-dot{width:12px;height:12px;border-radius:50%;background:var(--rose-text);flex:none}
.main-nav a{position:absolute;top:0;height:65px;line-height:68px;font-size:8.5px;color:var(--ink);text-decoration:none;text-align:center}
.main-nav a.active{background:var(--rose-nav);color:#fff}

/* hero */
.hero{left:0;top:65px;width:882px;height:349px;background:
  radial-gradient(ellipse 260px 220px at 560px 140px,#f1cdb8 0%,#e3b29a 45%,transparent 75%),
  linear-gradient(90deg,#d9472c 0%,#e9a24a 10%,#cfd0d6 22%,#e5dccf 50%,#8a7c6c 85%,#5a5048 100%)}
.hero-arrow{width:33px;height:33px;border-radius:50%;border:2px solid rgba(255,255,255,.7)}
.hero-caption{background:var(--caption);color:#fff;font-size:12px;height:30px;line-height:31px;padding:0 16px;letter-spacing:.2px}

/* news */
.news{left:0;top:414px;width:882px;height:73px;background:linear-gradient(#eef0f3,#e3e4e8);border-top:1px solid #d4d5d9;border-bottom:1px solid #d4d5d9}
.news-title{left:126px;top:427px;font-size:10.5px;color:var(--rose-text)}
.news-pager{left:588px;top:426px;font-size:9px;color:#777;letter-spacing:3px}
.news-text{left:127px;top:446px;width:480px;font-size:7px;line-height:15px;color:var(--ink)}
.news-btn{left:623px;top:434px;width:130px;height:34px;background:var(--rose-btn);border:1px solid #a8406a;color:#fff;font-size:10px;line-height:34px;text-align:center}

/* welcome */
.welcome-title{left:0;top:518px;width:882px;text-align:center;color:var(--blue);font-size:14px;line-height:19.5px}
.welcome-text{left:148px;top:571px;width:586px;text-align:center;font-size:7.8px;line-height:17px;color:var(--ink)}

/* features */
.feature-photo{top:646px;width:195px;height:132px}
.photo-learning{left:126px;background:linear-gradient(135deg,#e8eef2 0%,#c9d4b4 35%,#e4a88a 60%,#6e8fb8 100%)}
.photo-creativity{left:344px;background:linear-gradient(135deg,#e6d3a0 0%,#f0c2a8 35%,#e2573a 65%,#f0b032 100%)}
.photo-sharing{left:562px;background:linear-gradient(90deg,#bfe0ec 0%,#e6d9c8 40%,#f4e8d8 60%,#8fc2e0 100%)}
.feature-title{top:792px;font-size:12.5px;color:var(--blue)}
.feature-text{top:814px;width:185px;font-size:7.2px;line-height:14.4px;color:var(--ink)}

/* testimonials */
.clients{left:0;top:917px;width:882px;height:209px;background:var(--rose)}
.clients-title{left:0;top:946px;width:870px;text-align:center;color:#fff;font-size:14.5px}
.quote-mark{color:rgba(255,255,255,.45);font-size:34px;font-family:Georgia,"Times New Roman",serif;font-style:italic;font-weight:700}
.clients-text{left:215px;top:983px;width:446px;text-align:center;color:#fff;font-size:7.8px;line-height:16px}
.clients-name{left:0;top:1073px;width:870px;text-align:center;color:#fff;font-size:8px}
.clients-date{left:0;top:1087px;width:870px;text-align:center;color:#fff;font-size:8px;font-style:italic}

/* footer */
.site-footer{left:0;top:1126px;width:882px;height:74px;background:var(--footer)}
.footer-nav{left:128px;top:1148px;font-size:7.3px;color:#ddd;white-space:nowrap;word-spacing:1px}
.footer-nav span{margin:0 9px;color:#bbb}
.copyright{left:128px;top:1169px;font-size:7.3px;color:#bbb}
.social{top:1155px;width:20px;height:20px;border-radius:50%;background:#8a8a8a}
</style>
</head>
<body>

<header class="site-header abs">
  <div class="brand abs"><span class="brand-dot"></span><span>Puddle Jump Kidscare</span></div>
  <nav class="main-nav">
    <a class="active" href="#" style="left:327px;width:68px">About Us</a>
    <a href="#" style="left:399px;width:60px">Services</a>
    <a href="#" style="left:470px;width:80px">Hours and Fees</a>
    <a href="#" style="left:556px;width:60px">Policies</a>
    <a href="#" style="left:623px;width:60px">Photos</a>
    <a href="#" style="left:695px;width:70px">Testimonials</a>
  </nav>
</header>

<section class="hero abs" role="img" aria-label="Close-up photo of a toddler chewing a colourful ring toy"></section>
<div class="hero-arrow abs" style="left:50px;top:211px"></div>
<div class="hero-arrow abs" style="left:800px;top:211px"></div>
<svg class="abs" style="left:50px;top:211px" width="33" height="33" viewBox="0 0 33 33"><path d="M19 10 L12 16.5 L19 23" fill="none" stroke="rgba(255,255,255,.75)" stroke-width="2"/></svg>
<svg class="abs" style="left:800px;top:211px" width="33" height="33" viewBox="0 0 33 33"><path d="M13 10 L21 16.5 L13 23" fill="none" stroke="rgba(255,255,255,.75)" stroke-width="2"/></svg>
<div class="hero-caption abs" style="left:76px;top:323px">PUDDLE JUMP KIDSCARE</div>
<div class="hero-caption abs" style="left:76px;top:359px">A PLAYSPACE WHERE CHILDREN CAN PLAY, CREATE, AND IMAGINE!</div>

<section class="news abs"></section>
<h3 class="news-title abs" style="font-weight:400">Latest News</h3>
<div class="news-pager abs">‹ ›</div>
<p class="news-text abs">We are thrilled to have found a new cheerful space with a private backyard! It's large, sunny, and filled with outdoor play equipment such as a toddler slide, sand/water activity table, and lots of toys! Please stay...</p>
<a class="news-btn abs">Click here for more</a>

<h1 class="welcome-title abs" style="font-weight:400">Welcome to Puddle Jump Kidscare,<br>a playspace where children can play, create, and imagine!</h1>
<p class="welcome-text abs">Welcome to Puddle Jump Kidscare, a licensed Group Family Day Care, located in Riverbend's leafy North Hill. We are located on a pretty, tree-lined block on Alder Lane, between 5th and 6th Avenues. We are a few blocks from the Green Line tram and the Harbor Road bus route, and we offer flexible hourly childcare, making it as easy as possible for busy parents on the go to arrange their children's care.</p>

<div class="feature-photo photo-learning abs" role="img" aria-label="Photo of a teacher reading a picture book with young children"></div>
<div class="feature-photo photo-creativity abs" role="img" aria-label="Photo of children doing colourful paper crafts at a table"></div>
<div class="feature-photo photo-sharing abs" role="img" aria-label="Photo of two toddlers sharing art supplies"></div>

<h2 class="feature-title abs" style="left:127px;font-weight:400">Learning</h2>
<p class="feature-text abs" style="left:127px">We develop age-appropriate activities that introduce and strengthen academic and social skills.</p>
<h2 class="feature-title abs" style="left:345px;font-weight:400">Creativity</h2>
<p class="feature-text abs" style="left:345px">We offer children a wide range of creative opportunities including art projects, toddler yoga lessons, afternoon tea parties, dress up play, and a large selection of books and games.</p>
<h2 class="feature-title abs" style="left:563px;font-weight:400">Sharing</h2>
<p class="feature-text abs" style="left:563px;top:813px">We strive to include enrichment activities that extend your child's understanding of the world and their role in it. During our tea parties, for instance, we teach and emphasize good manners so that your child can learn their benefits as they grow.</p>

<section class="clients abs"></section>
<h2 class="clients-title abs" style="font-weight:400">What Clients Say</h2>
<div class="quote-mark abs" style="left:183px;top:965px">“</div>
<div class="quote-mark abs" style="left:680px;top:1033px">”</div>
<svg class="abs" style="left:129px;top:1012px" width="12" height="20" viewBox="0 0 12 20"><path d="M9 2 L3 10 L9 18" fill="none" stroke="rgba(255,255,255,.6)" stroke-width="1.2"/></svg>
<svg class="abs" style="left:740px;top:1012px" width="12" height="20" viewBox="0 0 12 20"><path d="M3 2 L9 10 L3 18" fill="none" stroke="rgba(255,255,255,.6)" stroke-width="1.2"/></svg>
<p class="clients-text abs">We would love to hear from you if your child has come to Puddle Jump! If you would like to leave a testimonial, please complete the Contact Us form on this page so we may post your message below. We would love to hear from you if your child has come to Puddle Jump! If you would like to leave a testimonial, please complete the Contact Us form on this page so we may post your message below.</p>
<div class="clients-name abs">Marla Quinley</div>
<div class="clients-date abs">Posted on 27 Mar 2014</div>

<footer class="site-footer abs"></footer>
<div class="footer-nav abs">Home<span>|</span>About Us<span>|</span>Services<span>|</span>Hours and Fees<span>|</span>Policies<span>|</span>Contact Us<span>|</span>Photos<span>|</span>Testimonials</div>
<div class="copyright abs">© Copyright. Puddle Jump Kidscare. 2014. All Rights Reserved.</div>
<div class="social abs" style="left:628px"></div>
<div class="social abs" style="left:655px"></div>
<div class="social abs" style="left:681px"></div>
<div class="social abs" style="left:708px"></div>
<div class="social abs" style="left:735px"></div>

</body>
</html>
```